QVR business card

Need a business card for a company that provides instructional design and elearning development services. The website is here: http://quorvane.studio/

I'm attaching a current logo, as well as the old business card design. While I like to keep it clean, the old design is too simplistic for my liking. The only idea I want to reuse from the old design is placing industry jargon on the back of the card, just need a better way to present it. But if you have other ideas for the back--feel free to experiment.

Please use the colors complementary to the color we have on the website. Thank you!

```html
<!DOCTYPE html>
<html lang="en">
<head>
<meta charset="utf-8">
<title>QVR Business Card</title>
<link rel="stylesheet" href="https://fonts.googleapis.com/css2?family=Open+Sans:wght@400;600;700;800&family=PT+Sans+Narrow:wght@400&display=swap">
<style>
  :root {
    --teal: #1db3b1;
    --teal-deep: #139c9a;
    --teal-soft: #3cc0bd;
    --gold: #d4c793;
    --ink: #2b2b2b;
    --paper: #ffffff;
    --backdrop: #2a2a2c;
  }
  * { margin: 0; padding: 0; box-sizing: border-box; }
  html, body {
    width: 1200px; height: 925px; overflow: hidden;
    background: var(--backdrop);
  }
  .canvas {
    position: relative; width: 1200px; height: 925px;
  }
  .card {
    position: absolute; left: 250px; width: 700px; height: 400px;
    overflow: hidden; border-radius: 3px;
    box-shadow: 0 10px 30px rgba(0,0,0,.45);
  }

  /* Back side */
  .card-back { top: 40px; background: var(--teal); color: var(--paper); }
  .card-back .glow {
    position: absolute; border-radius: 50%; background: var(--teal-soft); opacity: .35;
  }
  .glow-a { width: 260px; height: 220px; left: 360px; top: 120px; }
  .glow-b { width: 200px; height: 180px; left: 520px; top: 10px; }
  .headline {
    position: absolute; left: 40px; top: 46px;
    font-family: "Open Sans", sans-serif; font-weight: 800;
    line-height: .95; letter-spacing: 1px;
  }
  .headline span { display: block; }
  .headline .l1 { font-size: 58px; }
  .headline .l2 { font-size: 58px; }
  .headline .l3 { font-size: 100px; letter-spacing: 0; }
  .headline .l4 { font-size: 58px; }
  .back-divider {
    position: absolute; left: 268px; top: 40px; width: 1.5px; height: 320px;
    background: rgba(255,255,255,.75);
  }
  .jargon {
    position: absolute; left: 288px; top: 46px; list-style: none;
    font-family: "PT Sans Narrow", sans-serif; font-size: 35px;
    line-height: 52px; text-transform: uppercase; letter-spacing: 0;
    white-space: nowrap;
  }

  /* Front side */
  .card-front { top: 485px; background: var(--paper); }
  .brand {
    position: absolute; left: 60px; top: 78px;
    display: flex; align-items: center; gap: 16px;
  }
  .brand-mark { width: 46px; height: 46px; background: var(--teal); }
  .brand-name {
    font-family: "Open Sans", sans-serif; font-weight: 700; font-size: 60px;
    color: var(--gold); letter-spacing: 2px; line-height: 1;
  }
  .person {
    position: absolute; right: 52px; top: 92px; text-align: left;
    font-family: "Open Sans", sans-serif;
  }
  .person-name { font-weight: 700; font-size: 22px; color: var(--teal); letter-spacing: .5px; }
  .person-role { font-size: 15px; color: var(--ink); margin-left: 92px; margin-top: 2px; }
  .rule { position: absolute; left: 56px; top: 178px; width: 600px; height: 14px; }
  .contact {
    position: absolute; left: 62px; top: 236px; list-style: none;
    font-family: "Open Sans", sans-serif; font-size: 17px; color: var(--ink);
  }
  .contact li { display: flex; align-items: center; gap: 12px; height: 30px; }
  .contact svg { width: 20px; height: 20px; }
  .footer-band { position: absolute; left: 0; bottom: 0; width: 700px; height: 90px; }
  .website {
    position: absolute; right: 24px; bottom: 23px;
    font-family: "Open Sans", sans-serif; font-size: 14px; color: var(--paper);
    letter-spacing: 1px; white-space: nowrap;
  }
</style>
</head>
<body>
<main class="canvas">

  <section class="card card-back" aria-label="Card back">
    <div class="glow glow-a"></div>
    <div class="glow glow-b"></div>
    <h1 class="headline">
      <span class="l1">HOW</span>
      <span class="l2">CAN</span>
      <span class="l3">WE</span>
      <span class="l4">HELP?</span>
    </h1>
    <div class="back-divider"></div>
    <ul class="jargon">
      <li>Mobile Learning SCORM</li>
      <li>Instructional Design LMS</li>
      <li>MOOCs eLearning HTML5</li>
      <li>Adult Learning Theory</li>
      <li>Gamification Classroom</li>
      <li>xAPI Blended Learning</li>
    </ul>
  </section>

  <section class="card card-front" aria-label="Card front">
    <div class="brand">
      <span class="brand-mark"></span>
      <span class="brand-name">QVR</span>
    </div>
    <div class="person">
      <div class="person-name">MARLEN VASQUEZ</div>
      <div class="person-role">Managing Director</div>
    </div>
    <svg class="rule" viewBox="0 0 600 14">
      <circle cx="5" cy="7" r="4" fill="var(--gold)"/>
      <line x1="5" y1="7" x2="360" y2="7" stroke="var(--gold)" stroke-width="1.5"/>
      <line x1="360" y1="7" x2="600" y2="7" stroke="var(--teal)" stroke-width="3"/>
    </svg>
    <ul class="contact">
      <li>
        <svg viewBox="0 0 20 20"><rect width="20" height="20" rx="3" fill="var(--teal)"/><path d="M6 4.5c-1 .6-1.6 1.8-.8 3.8 1.1 2.8 3.2 4.9 5.8 6.3 1.9 1 3.2.5 3.9-.4l-2.2-2-1.5.8c-1.2-.6-2.3-1.7-3-3l.8-1.5L8 4z" fill="#fff"/></svg>
        555-014-2287
      </li>
      <li>
        <svg viewBox="0 0 20 20"><rect width="20" height="20" rx="3" fill="var(--teal)"/><rect x="4" y="6" width="12" height="8" fill="#fff"/><path d="M4 6l6 5 6-5" fill="none" stroke="var(--teal)" stroke-width="1.2"/></svg>
        mvasquez@quorvane.studio
      </li>
    </ul>
    <svg class="footer-band" viewBox="0 0 700 90" preserveAspectRatio="none">
      <path d="M420 90 C 450 90, 455 40, 495 40 L 700 40 L 700 90 Z" fill="var(--teal)"/>
      <path d="M0 84 L 405 84 C 435 84, 442 30, 485 30 L 700 30" fill="none" stroke="var(--gold)" stroke-width="4"/>
    </svg>
    <div class="website">www.quorvane.studio</div>
  </section>

</main>
</body>
</html>
```